Business card design needed

Family General Practitioner/ Family Physician.
Logo is the logo of the Noble Guild of Family Healers Oceania
http://kpltw.varendo.example/ImageShelf/marks/pages/NGFHO%20mark_jpg.htm
Updates

Project Deadline Extended
Reason: Just a bit more time to make changes and the weekend for me to look at things closely and to choose. Thanks, Orin

Thanks for all the submissions. So many of them are really works of art. Not one of them are not good. The ones that I am eliminating are the ones that I think are not suitable for me personally only, and because if I don't, it makes it very difficult to decide as many of you are also sending me slight variations of a card. I have just decided to choose a second place card too. Can't thank you all enough. Good luck, Orin. P.S - Working today till 10 pm as the card says :-), so probably won't be able to give a feedback till late Saturday night or Sunday morning here in Sydney, Australia. 

Project Deadline Extended
Reason: Just added a second place to the budget and realised that Australia is ahead of the rest of the world in the time zone (only :-) - don't want to offend anyone or start a debate!! ) , so Monday deadline will mean it will be a weekend for the rest of the world. Just wanted to give everyone more time to submit their best, especially since I will be picking a second card too. Can't thank everyone enough for the submissions. P.S - Not keen on photos on the card.

Industry/Entity Type

Business

Contact Information for Business Card

Dr. Orin Halvey M.B.B.S., F.N.G.F.H.O
Family General Practitioner
Address, timings, phone and fax number on the back.

Requirements
Must have
• Timings
Mon 7 am - 7 pm
Tues 7 am - 12 pm
Wed 7 am - 10 pm
Thurs 7 am - 12 pm
Fri 7 am - 8 pm
Sat 8 am - 10 pm
Sun - Off

```html
<!DOCTYPE html>
<html lang="en">
<head>
<meta charset="utf-8">
<title>Working Hours Card</title>
<link href="https://fonts.googleapis.com/css2?family=News+Cycle:wght@400;700&display=swap" rel="stylesheet">
<style>
  :root {
    --backdrop: #ece5d3;
    --card-navy: #2b4466;
    --band-blue: #2e5582;
    --heading-tan: #a89a7e;
    --text-cream: #d3cab4;
    --address-grey: #c9c5b9;
    --accent-orange: #f0922a;
  }
  html, body {
    margin: 0;
    padding: 0;
    width: 1200px;
    height: 960px;
    overflow: hidden;
    background: var(--backdrop);
    font-family: "News Cycle", "Arial Narrow", sans-serif;
  }
  .card {
    position: absolute;
    left: 138px;
    top: 220px;
    width: 924px;
    height: 520px;
    border-radius: 30px;
    overflow: hidden;
    background: var(--card-navy);
  }
  .hours-title {
    position: absolute;
    top: 30px;
    left: 0;
    width: 100%;
    margin: 0;
    text-align: center;
    font-weight: 700;
    font-size: 30px;
    letter-spacing: 0.3px;
    color: var(--heading-tan);
  }
  .schedule {
    position: absolute;
    left: 281px;
    top: 88px;
    margin: 0;
    padding: 0;
    list-style: none;
    color: var(--text-cream);
    font-size: 27px;
  }
  .schedule li {
    position: relative;
    width: 364px;
    height: 40.5px;
    line-height: 40.5px;
  }
  .day { position: absolute; left: 0; }
  .open { position: absolute; right: 105px; text-align: right; }
  .dash { position: absolute; left: 264px; }
  .close { position: absolute; right: 0; text-align: right; }
  .closed { position: absolute; left: 246px; }
  .contact-band {
    position: absolute;
    left: 0;
    top: 392px;
    width: 100%;
    height: 128px;
    background: var(--band-blue);
  }
  .address {
    position: absolute;
    top: 26px;
    width: 100%;
    margin: 0;
    text-align: center;
    font-size: 23px;
    color: var(--address-grey);
  }
  .line {
    position: absolute;
    top: 72px;
    margin: 0;
    font-size: 25px;
    color: var(--accent-orange);
    transform: translateX(-50%);
    white-space: nowrap;
  }
  .line.phone { left: 278px; }
  .line.fax { left: 663px; }
</style>
</head>
<body>
  <section class="card">
    <h2 class="hours-title">WORKING HOURS</h2>
    <ul class="schedule">
      <li><span class="day">Monday</span><span class="open">7 AM</span><span class="dash">-</span><span class="close">7 PM</span></li>
      <li><span class="day">Tuesday</span><span class="open">7 AM</span><span class="dash">-</span><span class="close">12 PM</span></li>
      <li><span class="day">Wednesday</span><span class="open">7 AM</span><span class="dash">-</span><span class="close">10 PM</span></li>
      <li><span class="day">Thursday</span><span class="open">7 AM</span><span class="dash">-</span><span class="close">12 PM</span></li>
      <li><span class="day">Friday</span><span class="open">7 AM</span><span class="dash">-</span><span class="close">8 PM</span></li>
      <li><span class="day">Saturday</span><span class="open">8 AM</span><span class="dash">-</span><span class="close">10 PM</span></li>
      <li><span class="day">Sunday</span><span class="closed">OFF</span></li>
    </ul>
    <div class="contact-band">
      <p class="address">Level 2, Willow Arcade, Brackenridge Plaza, Fernvale Heights, NSW 2999</p>
      <p class="line phone">PHONE: 02 5550 1847</p>
      <p class="line fax">FAX: 02 5550 1862</p>
    </div>
  </section>
</body>
</html>
```